Business Cards - Brightpath Horizon

need to design unique business card for my mortgage business. I need to design credit card style business card for my business or any unique idea that you might have

Target Market(s)

Home Loan customers

Industry/Entity Type

Mortgage Brokerage

Contact Information for Business Card

please design credit card style or very unique style business card

Colors

Designer to choose colors to be used in the design.

Requirements
Must have
• Name
• position
• Phone number
• fax number
• email address
• website address
• social media address
• All above fields will be provided once design in finalised

```html
<!DOCTYPE html>
<html lang="en">
<head>
<meta charset="utf-8">
<title>Brightpath Horizon – Business Card</title>
<link rel="stylesheet" href="https://fonts.googleapis.com/css2?family=Tinos:wght@400;700&family=Share+Tech+Mono&display=swap">
<style>
  :root {
    --page-bg: #1c1c1c;
    --card-bg: #ffffff;
    --brand-blue: #1a3dbf;
    --ink-blue: #1f3aa8;
    --accent-orange: #f08a1c;
    --text-grey: #4a4a4a;
    --tree-light: #d6ecf7;
    --tree-mid: #c3e2f2;
  }
  * { box-sizing: border-box; margin: 0; padding: 0; }
  html, body {
    width: 1200px; height: 901px; overflow: hidden;
    background: var(--page-bg);
  }
  .business-card {
    position: absolute; left: 100px; top: 132px;
    width: 1000px; height: 637px;
    background: var(--card-bg);
    border-radius: 28px;
    overflow: hidden;
    font-family: "Tinos", "Times New Roman", serif;
  }
  .tree-decoration {
    position: absolute; left: 580px; top: 40px;
    width: 410px; height: 580px;
    background: radial-gradient(ellipse 60% 45% at 50% 40%, var(--tree-mid), var(--tree-light) 70%, rgba(214,236,247,0) 100%);
    border-radius: 45% 45% 10% 10%;
  }
  .social-links { position: absolute; left: 66px; top: 74px; display: flex; gap: 6px; }
  .social-dot { width: 40px; height: 40px; border-radius: 50%; background: var(--brand-blue); }
  .person { position: absolute; right: 52px; top: 58px; text-align: right; }
  .person-name { font-weight: 700; font-size: 37px; color: var(--ink-blue); line-height: 1.1; }
  .person-title { font-size: 26px; color: var(--accent-orange); margin-top: 4px; }
  .card-number {
    position: absolute; left: 222px; top: 232px;
    font-family: "Share Tech Mono", monospace;
    font-size: 74px; letter-spacing: 8px; color: var(--brand-blue);
    line-height: 1;
  }
  .brand { position: absolute; left: 50px; top: 470px; display: flex; align-items: center; gap: 12px; }
  .brand-square { width: 30px; height: 30px; background: var(--accent-orange); flex: none; }
  .brand-name { font-size: 33px; line-height: 1.05; color: var(--brand-blue); font-weight: 400; }
  .contact { position: absolute; top: 490px; font-size: 24px; color: var(--text-grey); line-height: 1.55; }
  .contact-phone { left: 374px; }
  .contact-phone .label { color: var(--brand-blue); font-weight: 700; }
  .contact-address { left: 651px; }
  .divider { position: absolute; left: 346px; top: 576px; width: 610px; height: 2px; background: var(--accent-orange); }
  .website { position: absolute; left: 653px; top: 584px; font-size: 24px; font-weight: 700; color: var(--ink-blue); }
</style>
</head>
<body>
  <div class="business-card">
    <div class="tree-decoration" role="img" aria-label="Faint light-blue tree illustration"></div>

    <div class="social-links" aria-label="Social media">
      <span class="social-dot"></span><span class="social-dot"></span>
      <span class="social-dot"></span><span class="social-dot"></span>
    </div>

    <div class="person">
      <p class="person-name">DANIEL REYES</p>
      <p class="person-title">CEO/FOUNDER</p>
    </div>

    <p class="card-number">517 304 8261</p>

    <div class="brand">
      <span class="brand-square"></span>
      <p class="brand-name">BRIGHTPATH<br>HORIZON</p>
    </div>

    <div class="contact contact-phone">
      <p><span class="label">P:</span> 907 215 4463</p>
      <p>mail@example.com</p>
    </div>
    <div class="contact contact-address">
      <p>2190 Willow Crest Drive</p>
      <p>Juneau, Alaska 99801</p>
    </div>

    <div class="divider"></div>
    <p class="website">www.example.com</p>
  </div>
</body>
</html>
```